Brimora - Nutritious Snacks and Desserts

We need a creative e-commerce website in which all features--buttons, background, etc.--convey our message: We sell delicious, nutritious snacks and desserts that most closely comply with the paleo diet guidelines. Our first product is Nuttaree®--raw, vegan, paleo chocolate balls that are made of dates, coconut, and cocoa. Our products are organic, raw, irresistible and nutritious. We have several versions of Nuttaree® in development, as well as mousse, ice cream, and crackers. Our mission is to purvey basic healthy foods. Our motto is, "Fuel for the Bold Trail-Walker(tm)."

Target Market(s)

Health-conscious professionals who tend to shop at health food stores. Our products also meet the requirements of a gluten-free diet; and they also don't contain refined sugar, so shoppers with gluten and possibly sugar issues are incidental customers.

Industry/Entity Type

Health Product

Coding

Number of Pages Required

5+ page

Colors

Designer to choose colors to be used in the design.

Requirements
Must have
• We need at least a home page, a products page, an about-us page, a contact page, and a shopping cart page. We would like to be able to add products on our own later. We should be able to handle some basic coding, especially if it's just a matter of copying and modifying product pages. We would also like the ability in the future to add blogging pages, allowing us to write articles about health food and healthy lifestyle, thus attracting web-traffic (SEO).
• Other features we would like to have:
• Product photo slider on the hopepage
• Back-to-top button at the bottom of the home page
• Make sure the site is mobile-compatible
• A search bar at the top of the homepage
• "Create an account" and "Previous orders"--allowing customers to see their previous orders and reorder what they purchased in the past.
Nice to have
• We would like to convey the paleo theme without actually stating it anywhere. We'll add text as necessary, according to the page layout; you can use ipsum lorem for purpose of demonstration.

```html
<!DOCTYPE html>
<html lang="en">
<head>
<meta charset="utf-8">
<title>Brimora – Nutritious Snacks and Desserts</title>
<link rel="stylesheet" href="https://fonts.googleapis.com/css2?family=Raleway:wght@400;500;600;700;800&family=Open+Sans:wght@400;600;700&family=Dancing+Script:wght@700&family=Yanone+Kaffeesatz:wght@300;400&display=swap">
<style>
:root{
  --green:#5ea114;
  --green-light:#7cc21c;
  --green-dark:#3f7a0c;
  --ink:#4a4a4a;
  --grey:#6e6e6e;
  --grey-light:#9a9a9a;
  --line:#dcdcdc;
  --paper:#f3f3f1;
  --white:#ffffff;
  --dark:#2b2622;
  --wood:#3a302a;
}
*{box-sizing:border-box;margin:0;padding:0}
html,body{width:1200px;height:3529px;overflow:hidden}
body{position:relative;background:var(--white);font-family:"Open Sans",Arial,sans-serif;color:var(--ink)}
.abs{position:absolute}
a{color:inherit;text-decoration:none}
.btn{position:absolute;display:flex;align-items:center;justify-content:center;gap:10px;background:var(--green);color:var(--white);font:700 11px "Raleway",sans-serif;letter-spacing:.5px;text-transform:uppercase}
.btn svg{width:14px;height:10px}
.script{font-family:"Dancing Script",cursive;color:var(--green);font-weight:700}
.section-title{position:absolute;left:0;width:1200px;text-align:center}
.section-title .script{font-size:38px;line-height:1;display:block}
.section-title h2{font:800 42px "Raleway",sans-serif;color:#585858;letter-spacing:.5px;line-height:1;margin-top:2px}
.section-title .rule{width:58px;height:3px;background:var(--green);margin:14px auto 0}

/* top bar */
.topbar{top:0;left:0;width:1200px;height:47px;background:linear-gradient(90deg,var(--green-dark),var(--green) 60%,var(--green-light));color:var(--white);font-size:12px}
.topbar .phone{left:118px;top:15px;display:flex;gap:8px;align-items:center}
.topbar .links{right:178px;top:15px;display:flex;gap:26px}
.topbar .links span{display:flex;gap:7px;align-items:center}
.topbar svg{width:12px;height:12px;fill:var(--white)}

/* header */
.header{top:47px;left:0;width:1200px;height:141px;background:var(--white)}
.brand{left:118px;top:10px;width:150px;text-align:center}
.brand .mark{width:68px;height:68px;border-radius:50%;background:var(--green-light);margin:0 auto}
.brand .name{font:700 30px "Raleway",sans-serif;color:var(--green);margin-top:4px;line-height:1}
.nav{left:329px;top:62px;display:flex;align-items:center;font:500 15px "Raleway",sans-serif;color:#333}
.nav .dot{width:4px;height:4px;border-radius:50%;background:var(--green);margin:0 20px}
.nav .active{color:var(--green)}
.header .search{left:996px;top:60px;width:22px;height:22px}
.header .cart{left:1042px;top:58px;width:26px;height:26px}
.header .badge{left:1062px;top:54px;width:16px;height:16px;border-radius:50%;background:var(--green);color:#fff;font-size:9px;text-align:center;line-height:16px}

/* hero */
.hero{top:188px;left:0;width:1200px;height:440px;background:radial-gradient(ellipse at 62% 30%,#c98a3a 0,#8c5a2e 18%,#3a3430 42%,#2a2826 70%),#2a2826}
.hero .shade{left:0;bottom:0;width:1200px;height:106px;background:rgba(20,20,20,.72)}
.hero h1{left:118px;top:345px;font:800 36px "Raleway",sans-serif;color:var(--white);letter-spacing:.3px}
.hero h1 em{font-style:normal;color:var(--green-light)}
.hero p{left:118px;top:402px;font:400 14px "Raleway",sans-serif;color:#e8e8e8}
.hero .btn{left:953px;top:367px;width:127px;height:31px}
.hero .dots{left:1142px;top:178px;display:flex;flex-direction:column;gap:10px}
.hero .dots i{display:block;width:9px;height:9px;border-radius:50%;border:1px solid #ddd}
.hero .dots i.on{background:var(--green-light);border-color:var(--green-light)}

/* categories */
.categories{top:628px;left:0;width:1200px;height:796px;background:var(--paper)}
.categories .section-title{top:54px}
.cat-line{left:118px;top:205px;width:964px;height:1px;background:var(--line)}
.cat{position:absolute;top:175px;width:120px;text-align:center;font:500 13px "Raleway",sans-serif;color:var(--grey)}
.cat .icon{width:60px;height:60px;border-radius:50%;border:2px solid var(--green);background:var(--paper);margin:0 auto 12px;display:flex;align-items:center;justify-content:center}
.cat .icon svg{width:28px;height:28px;stroke:var(--green);fill:none;stroke-width:2}
.cat.on .icon{background:var(--green)}
.cat.on .icon svg{stroke:#fff}
.cat.on{color:var(--green)}
.product{position:absolute;top:301px;width:302px;height:389px;background:var(--white);box-shadow:0 1px 3px rgba(0,0,0,.08);text-align:center}
.product .photo{height:205px;background:linear-gradient(180deg,#bdb6a8,#e4ddce 50%,#8e8a7e)}
.product h3{font:700 16px "Raleway",sans-serif;color:#555;margin-top:22px;letter-spacing:.3px}
.product .stars{color:var(--green);font-size:14px;letter-spacing:2px;margin-top:6px}
.product .price{font:700 17px "Raleway",sans-serif;color:#555;margin-top:2px}
.product .sep{width:160px;height:1px;background:var(--line);margin:10px auto 0}
.product .btn{position:relative;margin:16px auto 0;width:140px;height:30px;font-size:9px}
.view-all{left:536px;top:718px;width:125px;height:30px;z-index:2}
.treeline{left:0;top:750px;width:1200px;height:46px;background:linear-gradient(180deg,rgba(94,161,20,0),var(--green) 85%)}

/* about */
.about{top:1424px;left:0;width:1200px;height:623px;background:linear-gradient(180deg,var(--green) 0,var(--green) 276px,var(--white) 276px)}
.about .section-title{top:36px}
.about .section-title .script{color:#d5f1a8;font-size:34px}
.about .section-title h2{color:var(--white)}
.about .section-title .rule{background:var(--white)}
.about-card{left:99px;top:141px;width:1002px;height:470px;background:var(--white);box-shadow:0 4px 18px rgba(0,0,0,.12)}
.about-card h3{position:absolute;left:89px;top:44px;font:300 46px/52px "Yanone Kaffeesatz",sans-serif;color:var(--green);letter-spacing:.5px}
.about-card p{position:absolute;left:89px;top:190px;width:420px;font-size:12.5px;line-height:19px;color:#555;text-align:justify}
.about-card .btn{left:89px;top:388px;width:165px;height:40px}
.about-photo{left:553px;top:47px;width:318px;height:318px;border-radius:50%;background:radial-gradient(circle at 50% 52%,#f2e3c0 0,#d9a860 30%,#3a3a3c 48%,#2a2a2c 100%)}
.about-badge{left:820px;top:330px;width:110px;height:110px;border-radius:50%;background:var(--white);box-shadow:0 2px 6px rgba(0,0,0,.15);display:flex;align-items:center;justify-content:center;font:700 18px "Raleway",sans-serif;color:var(--green)}

/* blog */
.blog{top:2047px;left:0;width:1200px;height:694px;background:var(--white)}
.blog .section-title{top:36px}
.post{position:absolute;top:160px;width:303px;height:452px;border:1px solid var(--line);background:var(--white)}
.post .date{position:absolute;right:14px;top:16px;font:600 9px "Raleway",sans-serif;color:#777;letter-spacing:.5px}
.post .photo{position:absolute;left:0;top:42px;width:301px;height:155px;background:linear-gradient(135deg,#4b3a2c,#9c8a6a 40%,#6d7b3a 60%,#3a2a22)}
.post h4{position:absolute;left:16px;top:230px;font:700 11.5px "Raleway",sans-serif;color:var(--green);letter-spacing:1px}
.post .tag{position:absolute;left:16px;top:249px;font:500 9px "Raleway",sans-serif;color:#888;letter-spacing:.5px}
.post p{position:absolute;left:16px;top:274px;width:268px;font-size:11px;line-height:17px;color:#666}
.post .more{position:absolute;left:16px;top:392px;width:111px;height:35px;border:1px solid var(--green);font:600 9px "Raleway",sans-serif;color:#555;display:flex;align-items:center;justify-content:center;letter-spacing:.5px}
.post .social{position:absolute;right:14px;top:401px;display:flex;gap:4px}
.post .social i{display:block;width:16px;height:16px;border-radius:50%;background:var(--green)}
.pager{left:529px;top:654px;display:flex;gap:10px}
.pager i{display:block;width:40px;height:2px;background:var(--line)}
.pager i.on{background:#b9b9b9}

/* contact */
.call{top:2741px;left:0;width:600px;height:464px;background:linear-gradient(135deg,var(--green),var(--green-dark));color:var(--white);text-align:center}
.call .ring{left:270px;top:68px;width:60px;height:60px}
.call .note{left:0;width:600px;top:160px;font-size:13px}
.call .number{left:172px;top:212px;width:393px;height:87px;border:3px solid var(--white);font:600 46px/81px "Open Sans",sans-serif;letter-spacing:1px}
.call .pin{left:288px;top:350px;width:24px;height:24px}
.call .addr{left:0;width:600px;top:384px;font-size:12px;line-height:19px}
.shout{top:2741px;left:600px;width:600px;height:464px;background:linear-gradient(135deg,#3a3a38,#262523 60%,#3c3a36)}
.shout .eyebrow{left:0;width:600px;top:70px;text-align:center;font:500 10px "Raleway",sans-serif;color:#ccc;letter-spacing:3px}
.shout h2{left:0;width:600px;top:92px;text-align:center;font:800 26px "Raleway",sans-serif;color:var(--green-light);letter-spacing:.5px}
.field{position:absolute;left:35px;width:396px;background:rgba(255,255,255,.55);font-size:11px;color:#333;padding:9px 10px}
.shout .submit{left:35px;top:363px;width:396px;height:35px}

/* footer */
.footer{top:3205px;left:0;width:1200px;height:282px;background:linear-gradient(90deg,#2e2620,#463a30 30%,#2f2721 60%,#43372d);color:#ddd}
.footer h5{position:absolute;top:68px;font:800 15px "Raleway",sans-serif;color:var(--green-light);letter-spacing:.5px}
.f-about{left:122px;top:100px;width:240px;font-size:10.5px;line-height:15px}
.f-about b{display:block;font:700 11px "Raleway",sans-serif;color:#fff;margin-bottom:8px}
.f-about .last{margin-top:14px}
.f-list{position:absolute;top:102px;font:500 11px "Raleway",sans-serif;color:#eee;text-transform:uppercase}
.f-list li{list-style:none;display:flex;align-items:center;gap:8px}
.f-list i{display:block;border-radius:50%;background:var(--green-light)}
.quick li{height:25px}
.quick i{width:12px;height:12px}
.connect li{height:35px}
.connect i{width:22px;height:22px}
.f-account{left:887px;top:66px;font:700 14px "Raleway",sans-serif;color:#fff;display:flex;gap:10px;align-items:center}
.f-bag{left:882px;top:116px;font:700 15px "Raleway",sans-serif;color:#fff;display:flex;gap:10px;align-items:center}
.f-email{left:882px;top:176px;width:200px;height:24px;background:#fff;font-size:9px;color:#777;padding:6px 8px}
.f-sub{left:922px;top:214px;width:113px;height:28px;font-size:9px}
.copyright{top:3487px;left:0;width:1200px;height:42px;background:var(--green);color:#eaf6d8;font-size:11px;text-align:center;line-height:42px}
</style>
</head>
<body>

<div class="abs topbar">
  <div class="abs phone"><svg viewBox="0 0 24 24"><path d="M6.6 10.8a15 15 0 006.6 6.6l2.2-2.2c.3-.3.7-.4 1-.2 1.1.4 2.3.6 3.6.6.6 0 1 .4 1 1V20c0 .6-.4 1-1 1A17 17 0 013 4c0-.6.4-1 1-1h3.5c.6 0 1 .4 1 1 0 1.3.2 2.5.6 3.6.1.3 0 .7-.2 1z"/></svg>(555) 014 – 2290</div>
  <div class="abs links">
    <span><svg viewBox="0 0 24 24"><circle cx="12" cy="8" r="4"/><path d="M4 21c0-4 4-7 8-7s8 3 8 7z"/></svg>Login / Sign up</span>
    <span><svg viewBox="0 0 24 24"><path d="M12 21l-8-8a5 5 0 017-7l1 1 1-1a5 5 0 017 7z"/></svg>Wishlist (0)</span>
    <span><svg viewBox="0 0 24 24"><path d="M3 4h3l2.5 11h10L21 7H8" fill="none" stroke="#fff" stroke-width="2"/><circle cx="10" cy="19" r="1.6"/><circle cx="17" cy="19" r="1.6"/></svg>Checkout</span>
  </div>
</div>

<header class="abs header">
  <div class="abs brand"><div class="mark"></div><div class="name">Brimora</div></div>
  <nav class="abs nav">
    <a class="active">HOME</a><span class="dot"></span><a>ABOUT US</a><span class="dot"></span><a>PRODUCTS</a><span class="dot"></span><a>BLOG</a><span class="dot"></span><a>CONTACT US</a>
  </nav>
  <svg class="abs search" viewBox="0 0 24 24" fill="none" stroke="#444" stroke-width="2"><circle cx="10" cy="10" r="7"/><path d="M15 15l6 6"/></svg>
  <svg class="abs cart" viewBox="0 0 24 24" fill="none" stroke="#444" stroke-width="1.8"><path d="M5 8h14l-1 13H6z"/><path d="M9 8V6a3 3 0 016 0v2"/></svg>
  <div class="abs badge">2</div>
</header>

<section class="abs hero">
  <div class="abs" role="img" aria-label="Bowl of colourful paleo food on a dark wooden table" style="inset:0"></div>
  <div class="abs dots"><i class="on"></i><i></i><i></i><i></i></div>
  <div class="abs shade"></div>
  <h1 class="abs">WELCOME TO <em>BRIMORA FOODS.</em></h1>
  <p class="abs">Fuel for the Bold Trail-Walker™</p>
  <a class="btn">Get Started <svg viewBox="0 0 14 10" fill="none" stroke="#fff" stroke-width="1.5"><path d="M0 5h12M8 1l4 4-4 4"/></svg></a>
</section>

<section class="abs categories">
  <div class="section-title"><span class="script">Product</span><h2>CATEGORIES</h2><div class="rule"></div></div>
  <div class="abs cat-line"></div>
  <div class="cat on" style="left:319px"><div class="icon"><svg viewBox="0 0 24 24"><path d="M4 10h16l-2 10H6z"/><path d="M8 10c0-3 2-5 4-5s4 2 4 5"/></svg></div>Nuttaree®</div>
  <div class="cat" style="left:467px"><div class="icon"><svg viewBox="0 0 24 24"><path d="M6 12h12l-2 9H8z"/><path d="M7 12c0-4 2-7 5-8 3 1 5 4 5 8"/></svg></div>Mousse</div>
  <div class="cat" style="left:613px"><div class="icon"><svg viewBox="0 0 24 24"><rect x="4" y="4" width="12" height="12" rx="1"/><rect x="8" y="8" width="12" height="12" rx="1"/></svg></div>Crackers</div>
  <div class="cat" style="left:757px"><div class="icon"><svg viewBox="0 0 24 24"><circle cx="12" cy="8" r="5"/><path d="M7 10l5 12 5-12"/></svg></div>Ice cream</div>

  <div class="product" style="left:118px"><div class="photo" role="img" aria-label="Nuttaree tub on a tiled counter"></div><h3>NUTTAREE®</h3><div class="stars">★★★★★</div><div class="price">$80.00</div><div class="sep"></div><a class="btn">Add to cart <svg viewBox="0 0 14 10" fill="none" stroke="#fff" stroke-width="1.3"><path d="M1 1h2l1.5 6h7L13 3H4"/></svg></a></div>
  <div class="product" style="left:445px"><div class="photo" role="img" aria-label="Nuttaree tub on a tiled counter"></div><h3>NUTTAREE®</h3><div class="stars">★★★★★</div><div class="price">$80.00</div><div class="sep"></div><a class="btn">Add to cart <svg viewBox="0 0 14 10" fill="none" stroke="#fff" stroke-width="1.3"><path d="M1 1h2l1.5 6h7L13 3H4"/></svg></a></div>
  <div class="product" style="left:774px"><div class="photo" role="img" aria-label="Nuttaree tub on a tiled counter"></div><h3>NUTTAREE®</h3><div class="stars">★★★★★</div><div class="price">$80.00</div><div class="sep"></div><a class="btn">Add to cart <svg viewBox="0 0 14 10" fill="none" stroke="#fff" stroke-width="1.3"><path d="M1 1h2l1.5 6h7L13 3H4"/></svg></a></div>

  <div class="abs treeline" role="img" aria-label="Green landscape silhouette of trees and wind turbines"></div>
  <a class="btn view-all">View All <svg viewBox="0 0 14 10" fill="none" stroke="#fff" stroke-width="1.5"><path d="M0 5h12M8 1l4 4-4 4"/></svg></a>
</section>

<section class="abs about">
  <div class="section-title"><span class="script">About</span><h2>BRIMORA FOOD</h2><div class="rule"></div></div>
  <div class="abs about-card">
    <h3>FUEL FOR THE<br>BOLD TRAIL-WALKER™</h3>
    <p>Lorem Ipsum is simply dummy text of the printing and typesetting industry. Lorem Ipsum has been the industry's standard dummy text ever since the 1500s, when an unknown printer took a galley of type and scrambled it to make a type specimen book. It has survived not only five centuries, but also the leap into electronic typesetting, remaining essentially unchanged. It was popularised in the 1960s with the release of Letraset sheets containing Lorem Ipsum passages.</p>
    <a class="btn">Read More <svg viewBox="0 0 14 10" fill="none" stroke="#fff" stroke-width="1.5"><path d="M0 5h12M8 1l4 4-4 4"/></svg></a>
    <div class="abs about-photo" role="img" aria-label="Stack of pancakes topped with blueberries and cream"></div>
    <div class="abs about-badge">Brimora</div>
  </div>
</section>

<section class="abs blog">
  <div class="section-title"><span class="script">Latest from</span><h2>THE BLOG</h2><div class="rule"></div></div>

  <article class="post" style="left:118px"><div class="date">MAY 10, 2018, WEDNESDAY</div><div class="photo" role="img" aria-label="Plate of grilled bread and beet salad"></div><h4>LOREM IPSUM DOLOR SIT AMET</h4><div class="tag">FOOD / PORTFOLIO</div><p>Lorem ipsum dolor sit amet, consectetur adipiscing elit. Sed euismod in tellus in mattis. Aliquam erat volutpat. Praesent ultricies aliquet erat a semper.</p><a class="more">READ MORE</a><div class="social"><i></i><i></i><i></i><i></i></div></article>
  <article class="post" style="left:447px"><div class="date">MAY 10, 2018, WEDNESDAY</div><div class="photo" role="img" aria-label="Plate of grilled bread and beet salad"></div><h4>LOREM IPSUM DOLOR SIT AMET</h4><div class="tag">FOOD / PORTFOLIO</div><p>Lorem ipsum dolor sit amet, consectetur adipiscing elit. Sed euismod in tellus in mattis. Aliquam erat volutpat. Praesent ultricies aliquet erat a semper.</p><a class="more">READ MORE</a><div class="social"><i></i><i></i><i></i><i></i></div></article>
  <article class="post" style="left:779px"><div class="date">MAY 10, 2018, WEDNESDAY</div><div class="photo" role="img" aria-label="Plate of grilled bread and beet salad"></div><h4>LOREM IPSUM DOLOR SIT AMET</h4><div class="tag">FOOD / PORTFOLIO</div><p>Lorem ipsum dolor sit amet, consectetur adipiscing elit. Sed euismod in tellus in mattis. Aliquam erat volutpat. Praesent ultricies aliquet erat a semper.</p><a class="more">READ MORE</a><div class="social"><i></i><i></i><i></i><i></i></div></article>

  <div class="abs pager"><i class="on"></i><i></i><i></i></div>
</section>

<section class="abs call">
  <svg class="abs ring" viewBox="0 0 24 24" fill="#fff"><path d="M6.6 10.8a15 15 0 006.6 6.6l2.2-2.2c.3-.3.7-.4 1-.2 1.1.4 2.3.6 3.6.6.6 0 1 .4 1 1V20c0 .6-.4 1-1 1A17 17 0 013 4c0-.6.4-1 1-1h3.5c.6 0 1 .4 1 1 0 1.3.2 2.5.6 3.6.1.3 0 .7-.2 1z"/></svg>
  <div class="abs note">24/7 Assistance. Call us any time.</div>
  <div class="abs number">(555) 014-229</div>
  <svg class="abs pin" viewBox="0 0 24 24" fill="none" stroke="#fff" stroke-width="1.6"><rect x="1" y="1" width="22" height="22" rx="2"/><path d="M12 19s-5-5-5-8.5a5 5 0 0110 0C17 14 12 19 12 19z"/><circle cx="12" cy="10.5" r="1.8"/></svg>
  <div class="abs addr">48 ORCHARD LANE<br>FAIRHAVEN, OR 97001</div>
</section>

<section class="abs shout" role="img" aria-label="Dim photo of a plated meal behind the contact form">
  <div class="abs eyebrow">- CONTACT US -</div>
  <h2 class="abs">GIVE US A SHOUT</h2>
  <div class="field" style="top:198px;height:38px">Enter Name</div>
  <div class="field" style="top:243px;height:38px">Enter Email</div>
  <div class="field" style="top:287px;height:66px">Enter Message</div>
  <a class="btn submit">Submit <svg viewBox="0 0 14 10" fill="none" stroke="#fff" stroke-width="1.5"><path d="M0 5h12M8 1l4 4-4 4"/></svg></a>
</section>

<footer class="abs footer" role="img" aria-label="Dark wood texture footer">
  <h5 style="left:122px">ABOUT US</h5>
  <div class="abs f-about"><b>BRIMORA FOODS</b>Our products are raw, organic, vegan, gluten-free, dairy-free, fiber-rich, nutrient-dense, antioxidant-rich real foods with no preservatives, no added sugar, and no artificial or plant-based sweeteners.<div class="last">And they are irresistibly scrumptious!</div></div>
  <h5 style="left:400px">QUICK LINKS</h5>
  <ul class="f-list quick" style="left:400px"><li><i></i>Home</li><li><i></i>About Us</li><li><i></i>Products</li><li><i></i>Blog</li><li><i></i>Contact Us</li></ul>
  <h5 style="left:631px">CONNECT WITH US</h5>
  <ul class="f-list connect" style="left:631px;top:98px"><li><i></i>Circlenet</li><li><i></i>Chirpline</li><li><i></i>Photolane</li><li><i></i>Globelink</li></ul>
  <div class="abs f-account"><svg width="14" height="14" viewBox="0 0 24 24" fill="var(--green-light)"><path d="M10 17l5-5-5-5v3H2v4h8zM14 3h6v18h-6v-2h4V5h-4z"/></svg>LOGIN <span style="color:#aaa">|</span> <svg width="12" height="14" viewBox="0 0 24 24" fill="var(--green-light)"><circle cx="12" cy="7" r="5"/><path d="M3 22c0-5 4-8 9-8s9 3 9 8z"/></svg>REGISTER</div>
  <div class="abs f-bag"><svg width="22" height="22" viewBox="0 0 24 24" fill="var(--green-light)"><path d="M4 8h16l-1 14H5z"/><path d="M8 8V6a4 4 0 018 0v2" fill="none" stroke="var(--green-light)" stroke-width="2"/></svg>SHOPPING BAG (0)</div>
  <div class="abs f-email">YOUR E-MAIL</div>
  <a class="btn f-sub">Subscribe <svg viewBox="0 0 14 10" fill="none" stroke="#fff" stroke-width="1.5"><path d="M0 5h12M8 1l4 4-4 4"/></svg></a>
</footer>

<div class="abs copyright">© 2018 Brimora Foods.. All Right Reserved.</div>

</body>
</html>
```